Business Broker Graphics Package

Hi,

Seeking a smart and professional graphics package design including business card design (double-sided) and letterhead and PowerPoint slide template.

3 Deliverables:

1. Company Letterhead
2. Business Card (two sided) (will consider one sided designs)
3. PowerPoint Template. Requires cover PPT and 2nd page design.

For the prototype use this info:
Marcus Dellorane RPA
Registered Practice Adviser
5678 Harlow Rd.
Tampa, FL 77777
555.014.2273
Demo@Quillbrookpath.com
www.QuillbrookPath.com

I'll give exact information to winner to finalize later.

I've attached the logo..

Business card will be double sided and info for back of card is in attachment.

Look forward to your great ideas and concepts!

Target Market(s)

President's and business owners, CPA's and other professionals.

Industry/Entity Type

Business

Requirements
Nice to have
• Prefer horizontal card, but will consider vertical card design.

The business card should be all or primarily white. Text colors should be same as logo creative combination of black and forest green.

PowerPoint can be white background or lighter palette of colors I like gold color. I do not like darkly colored PowerPoint designs I prefer light and bright designs.

```html
<!DOCTYPE html>
<html lang="en">
<head>
<meta charset="utf-8">
<title>Quillbrook Path – Business Card</title>
<link rel="stylesheet" href="https://fonts.googleapis.com/css2?family=Roboto:wght@400;500&family=Cinzel:wght@600&display=swap">
<style>
  :root {
    --backdrop: #9b9b9b;
    --card: #ffffff;
    --ink: #1a1a1a;
    --ink-soft: #3a3a3a;
    --muted: #555555;
    --rule: #d6d6d6;
    --forest: #14452b;
    --band-dark: #1e1e1e;
  }
  html, body {
    margin: 0;
    width: 1200px;
    height: 1000px;
    overflow: hidden;
    background: var(--backdrop);
  }
  .card {
    position: absolute;
    left: 402px;
    top: 370px;
    width: 384px;
    height: 225px;
    background: var(--card);
    box-shadow: 1px 2px 4px rgba(0,0,0,0.35);
    overflow: hidden;
    font-family: "Roboto", Arial, sans-serif;
  }
  .brand {
    position: absolute;
    left: 27px;
    top: 70px;
  }
  .brand-name {
    margin: 0;
    font-size: 22px;
    font-weight: 500;
    color: var(--forest);
    letter-spacing: 0.3px;
    line-height: 1;
  }
  .brand-tagline {
    margin: 4px 0 0;
    font-size: 8px;
    font-weight: 500;
    color: var(--ink);
    letter-spacing: 0.2px;
  }
  .divider {
    position: absolute;
    left: 25px;
    top: 116px;
    width: 208px;
    height: 1px;
    background: var(--rule);
  }
  .holder {
    position: absolute;
    left: 228px;
    top: 88px;
  }
  .holder-name {
    margin: 0;
    font-size: 13px;
    font-weight: 400;
    color: var(--ink-soft);
    letter-spacing: 0.3px;
  }
  .holder-title {
    margin: 5px 0 0 15px;
    font-size: 8.5px;
    color: var(--ink);
  }
  .contacts {
    position: absolute;
    left: 23px;
    top: 129px;
    margin: 0;
    padding: 0;
    list-style: none;
  }
  .contacts li {
    display: flex;
    align-items: center;
    height: 16.5px;
    font-size: 9.5px;
    color: var(--muted);
  }
  .contacts svg {
    width: 13px;
    height: 13px;
    margin-right: 5px;
    flex: none;
  }
  .footer-band {
    position: absolute;
    left: 0;
    bottom: 0;
    width: 384px;
    height: 16px;
  }
  .footer-slogan {
    position: absolute;
    left: 241px;
    bottom: 3px;
    margin: 0;
    font-family: "Cinzel", "Times New Roman", serif;
    font-weight: 600;
    font-size: 9px;
    color: #ffffff;
    letter-spacing: 0.4px;
  }
</style>
</head>
<body>
  <div class="card">
    <div class="brand">
      <p class="brand-name">Quillbrook Path</p>
      <p class="brand-tagline">MERGER ACQUISITION GROWTH EXPERTS</p>
    </div>
    <div class="divider"></div>

    <div class="holder">
      <p class="holder-name">Marcus Dellorane RPA</p>
      <p class="holder-title">Registered Practice Adviser</p>
    </div>

    <ul class="contacts">
      <li>
        <svg viewBox="0 0 13 13" aria-hidden="true"><rect width="13" height="13" rx="1.5" fill="var(--forest)"/><rect x="4" y="2" width="5" height="9" rx="1" fill="none" stroke="#fff" stroke-width="1.2"/></svg>
        555.014.2273
      </li>
      <li>
        <svg viewBox="0 0 13 13" aria-hidden="true"><rect width="13" height="13" rx="1.5" fill="var(--forest)"/><path d="M6.5 11.5 L3.6 6.6 A3.2 3.2 0 1 1 9.4 6.6 Z" fill="#fff"/><circle cx="6.5" cy="5" r="1.2" fill="var(--forest)"/></svg>
        5678 Harlow Rd. Tampa, FL 77777
      </li>
      <li>
        <svg viewBox="0 0 13 13" aria-hidden="true"><rect width="13" height="13" rx="1.5" fill="var(--forest)"/><rect x="2.5" y="4" width="8" height="5.5" fill="#fff"/><path d="M2.5 4 L6.5 7 L10.5 4" fill="none" stroke="var(--forest)" stroke-width="0.9"/></svg>
        Demo@Quillbrookpath.com
      </li>
      <li>
        <svg viewBox="0 0 13 13" aria-hidden="true"><rect width="13" height="13" rx="1.5" fill="var(--forest)"/><circle cx="6.5" cy="6.5" r="4" fill="none" stroke="#fff" stroke-width="1"/><path d="M2.5 6.5 H10.5 M6.5 2.5 C4.5 5 4.5 8 6.5 10.5 M6.5 2.5 C8.5 5 8.5 8 6.5 10.5" fill="none" stroke="#fff" stroke-width="0.8"/></svg>
        www.QuillbrookPath.com
      </li>
    </ul>

    <svg class="footer-band" viewBox="0 0 384 16" aria-hidden="true">
      <polygon points="0,0 226,0 220,16 0,16" fill="var(--band-dark)"/>
      <polygon points="230,0 384,0 384,16 224,16" fill="var(--forest)"/>
    </svg>
    <p class="footer-slogan">Ownership Solutions</p>
  </div>
</body>
</html>
```